New Business Card for Web Design/Internet Marketing Company

Looking for a great looking new business card. We are a 10 year old web design, internet marketing and website management company that works mostly with small businesses.

Our new card needs to better match the colors and style of our website, be bold, extremely usable and slightly edgy.

Target Market(s)

Small/Medium businesses that have websites

Industry/Entity Type

Internet

Requirements
Must have
• Front and back design, full color, rounded corners please

Must use the colors/style of our website (JPG provided)

INFO FOR CARDS (as readable as possible please)
Mark Lenner
President/CEO
mark@trelvanmedia.example
Phone: 520-381-7459
Toll Free: 866-381-7459
Address: 4315 W. Calloway Ave. Ste. 140, Tucson, AZ 85792

THINGS I WANT TO PROMOTE (if there is room):
1. Our Website - www.trelvanmedia.example

2. Social Media
Twitter: @trelvanmedia
Facebook: www.facebook.com/trelvanmedia

3. Our Services
Web Design
Internet Marketing
Website Management

```html
<!DOCTYPE html>
<html lang="en">
<head>
<meta charset="utf-8">
<title>Trelvan Media – Business Card</title>
<link href="https://fonts.googleapis.com/css2?family=Source+Sans+3:ital,wght@0,400;0,600;0,700;1,400&display=swap" rel="stylesheet">
<style>
  :root{
    --bg:#e9ebee;
    --card:#ffffff;
    --blue:#1b8fc9;
    --navy:#1f2f86;
    --orange:#f2892b;
    --ink:#333333;
    --grey:#6b6b6b;
  }
  *{box-sizing:border-box;margin:0;padding:0}
  html,body{width:1200px;height:944px;overflow:hidden}
  body{background:var(--bg);font-family:"Source Sans 3",Arial,sans-serif;color:var(--ink);position:relative}
  .card{position:absolute;width:600px;height:343px;background:var(--card);border-radius:26px;box-shadow:0 6px 18px rgba(0,0,0,.18);overflow:hidden}
  .card--front{left:80px;top:110px}
  .card--back{left:520px;top:490px}

  .brand{display:flex;align-items:center;gap:12px}
  .brand__dot{width:34px;height:34px;border-radius:50%;background:var(--orange);flex:none}
  .brand__name{color:var(--blue);font-weight:700;letter-spacing:-.5px;line-height:1;white-space:nowrap}
  .tagline{color:var(--grey);font-size:17px;font-style:italic;white-space:nowrap}

  .front__brand{position:absolute;left:0;right:0;top:78px;justify-content:center}
  .front__brand .brand__dot{width:52px;height:52px}
  .front__brand .brand__name{font-size:58px}
  .front__tagline{position:absolute;left:0;right:0;top:150px;text-align:center;font-size:20px}
  .front__url{position:absolute;left:0;right:0;top:222px;text-align:center;font-size:17px;font-weight:600;letter-spacing:.5px;color:var(--ink)}
  .services{position:absolute;left:0;right:0;top:250px;text-align:center;font-size:17px;color:var(--orange);letter-spacing:.3px}
  .services__sep{color:var(--blue);margin:0 5px}

  .back__brand{position:absolute;left:110px;top:30px}
  .back__brand .brand__name{font-size:40px}
  .back__tagline{position:absolute;left:370px;top:80px}
  .person{position:absolute;left:62px;top:114px}
  .person__name{font-size:22px;font-weight:600;color:var(--ink)}
  .person__title{font-size:14px;font-style:italic;color:var(--orange)}
  .address{position:absolute;left:40px;top:178px;display:flex;gap:8px;font-size:14px;line-height:1.3}
  .address svg{margin-top:2px;flex:none}
  .contacts{position:absolute;left:292px;top:138px;list-style:none;font-size:14px;line-height:19px}
  .contacts li{display:flex;align-items:center;gap:9px;white-space:nowrap}
  .contacts svg{flex:none}
  .contacts .hl{color:var(--orange)}
  .swoosh{position:absolute;left:0;bottom:0}
</style>
</head>
<body>

<section class="card card--front">
  <div class="brand front__brand">
    <span class="brand__dot"></span>
    <span class="brand__name">Trelvan Media</span>
  </div>
  <p class="tagline front__tagline">Grow your Business</p>
  <p class="front__url">www.trelvanmedia.example</p>
  <p class="services">Web Design<span class="services__sep">•</span>Internet Marketing<span class="services__sep">•</span>Website Management</p>
</section>

<section class="card card--back">
  <div class="brand back__brand">
    <span class="brand__dot"></span>
    <span class="brand__name">Trelvan Media</span>
  </div>
  <p class="tagline back__tagline">Grow your Business</p>

  <div class="person">
    <p class="person__name">Mark Lenner</p>
    <p class="person__title">President/CEO</p>
  </div>

  <div class="address">
    <svg width="14" height="13" viewBox="0 0 14 13"><path d="M7 0 L14 6 H12 V13 H8.5 V9 H5.5 V13 H2 V6 H0 Z" fill="var(--navy)"/></svg>
    <p>4315 W. Calloway Ave. Ste. 140<br>Tucson, AZ 85792</p>
  </div>

  <ul class="contacts">
    <li><svg width="13" height="10" viewBox="0 0 13 10"><rect x=".5" y=".5" width="12" height="9" fill="none" stroke="var(--navy)"/><path d="M.5 .5 L6.5 5.5 L12.5 .5" fill="none" stroke="var(--navy)"/></svg>mark@trelvanmedia.example</li>
    <li><svg width="13" height="13" viewBox="0 0 13 13"><path d="M3 1 L5 4 L4 5.5 Q5.5 8 7.5 9 L9 8 L12 10 L10.5 12 Q4 11 1 2.5 Z" fill="var(--navy)"/></svg>520-381-7459</li>
    <li><svg width="13" height="13" viewBox="0 0 13 13"><path d="M3 1 L5 4 L4 5.5 Q5.5 8 7.5 9 L9 8 L12 10 L10.5 12 Q4 11 1 2.5 Z" fill="var(--navy)"/></svg>866-381-7459 (toll free)</li>
    <li><svg width="13" height="13" viewBox="0 0 13 13"><circle cx="6.5" cy="6.5" r="6" fill="var(--navy)"/></svg>@trelvanmedia</li>
    <li><svg width="13" height="13" viewBox="0 0 13 13"><rect width="13" height="13" fill="var(--navy)"/></svg><span>www.<span class="hl">friendhub.example</span>/trelvanmedia</span></li>
  </ul>

  <svg class="swoosh" width="600" height="80" viewBox="0 0 600 80">
    <path d="M0 18 C150 58 330 8 600 18 L600 30 C330 22 160 72 0 34 Z" fill="var(--orange)"/>
    <path d="M0 40 C160 78 340 30 600 36 L600 80 L0 80 Z" fill="var(--navy)"/>
  </svg>
</section>

</body>
</html>
```